Judicial election website to attract voters

I need a simple one-page web design for a judicial election. I'm going to put up one picture, maybe two. The picture I have needs a little touch-up (whiten teeth for example). I have 3 paragraphs of text. I'd like a "Donate" button that can link to a CoinDrift account. I'd also like a little background design, like the Constitution or something like that. There's a couple other little things but that's the bulk of it.

Target Market(s)

Involved voters and some media

Industry/Entity Type

Legal

Number of Pages Required

1 page

Font styles to use
Sans Serif

Requirements
Must have
• My picture, text, donate button
• Phrase "Remember to vote August 30, 2016!"
Nice to have
• Perhaps a second photo, maybe a short 30 second video of me talking directly to the voters, cool background: Constitution, something judgey.
Should not have
• Not sure ... profanity, I guess.

```html
<!DOCTYPE html>
<html lang="en">
<head>
<meta charset="utf-8">
<title>Renata for Judge</title>
<link rel="stylesheet" href="https://fonts.googleapis.com/css2?family=Cinzel:wght@400;700&family=Open+Sans:wght@400;600&display=swap">
<style>
  :root{
    --navy:#1b1f4d;
    --navy-deep:#0f1633;
    --red:#c8101a;
    --white:#ffffff;
    --text:#333333;
    --muted:#6a6a6a;
    --footer:#333333;
    --topbar:#1d2140;
  }
  *{margin:0;padding:0;box-sizing:border-box}
  html,body{width:693px;height:1200px;overflow:hidden;background:var(--white)}
  body{font-family:"Open Sans",Arial,sans-serif;color:var(--text);position:relative}
  h2,h3{font-weight:400}

  .topbar{height:24px;background:linear-gradient(90deg,var(--topbar) 0%,#2a2e55 60%,#7a2230 78%,#2a2e55 100%);color:var(--white);font-size:7px;display:flex;align-items:center;justify-content:space-between;padding:0 76px}
  .topbar .contact{display:flex;gap:14px;align-items:center}
  .topbar .contact span{display:flex;align-items:center;gap:5px}
  .topbar .actions{display:flex;gap:6px}

  .site-header{height:56px;display:flex;align-items:center;justify-content:space-between;padding:0 76px;background:var(--white)}
  .brand{display:flex;align-items:center;gap:9px}
  .brand .mark{width:28px;height:28px;border-radius:50%;background:var(--red)}
  .brand .name{font-family:"Cinzel",Georgia,serif;font-size:16px;color:var(--navy);letter-spacing:1px}
  .main-nav{display:flex;gap:30px;font-family:"Cinzel",Georgia,serif;font-size:7px;letter-spacing:.4px}
  .main-nav a{color:#444;text-decoration:none}
  .main-nav a.active{color:var(--red)}

  .hero{height:265px;position:relative;overflow:hidden;background:linear-gradient(100deg,#0c0f2e 0%,#1e2458 35%,#3a3f78 52%,#8c2c3e 68%,#c9cad6 80%,#b0283a 100%)}
  .hero .portrait{position:absolute;right:0;top:0;width:340px;height:265px;background:radial-gradient(ellipse at 62% 30%,#e8b9a4 0%,#d9a68e 22%,#c9b89c 34%,rgba(214,110,90,.9) 55%,rgba(200,90,72,0) 80%)}
  .hero .copy{position:absolute;left:76px;top:88px;color:var(--white)}
  .hero .kicker{font-family:"Cinzel",Georgia,serif;font-size:14px;letter-spacing:1px}
  .hero .date{font-family:"Cinzel",Georgia,serif;font-size:30px;margin-top:6px;letter-spacing:.5px}
  .hero .dots{display:flex;gap:4px;margin-top:10px}
  .hero .dots i{display:block;width:19px;height:2px;background:rgba(255,255,255,.45)}
  .hero .dots i.on{background:var(--white)}

  .about{height:157px;text-align:center;padding-top:20px}
  .section-title{font-family:"Cinzel",Georgia,serif;font-size:19px;color:var(--navy);letter-spacing:.5px}
  .section-title em{font-style:normal;color:var(--red)}
  .about p{width:542px;margin:9px auto 0;font-size:5.4px;line-height:11px;color:#444}
  .btn{display:inline-block;background:var(--red);color:var(--white);border-radius:2px;text-decoration:none;font-family:"Open Sans",Arial,sans-serif}
  .about .btn{margin-top:15px;font-size:6px;padding:6px 13px}

  .video-band{height:355px;position:relative;text-align:center;background:linear-gradient(180deg,#1d2756 0%,#283468 45%,#121a3a 75%,#0c1330 100%)}
  .video-band .watch{font-family:"Cinzel",Georgia,serif;color:var(--white);font-size:16px;letter-spacing:1px;padding-top:50px}
  .player{position:absolute;left:204px;top:99px;width:285px;height:155px;background:#111}
  .player .screen{height:143px;background:linear-gradient(135deg,#1c3fae 0%,#2a62d6 50%,#1d3ea0 70%,#b8283b 85%,#e7e7ee 100%)}
  .player .play{position:absolute;left:125px;top:54px}
  .player .controls{height:12px;display:flex;align-items:center;gap:6px;padding:0 5px;color:#ddd;font-size:4.5px;background:#1a1a1a}
  .player .track{flex:1;height:3px;background:#444;position:relative}
  .player .track b{position:absolute;left:0;top:0;height:3px;width:24%;background:#aaa}
  .video-band .btn{position:absolute;left:312px;top:282px;font-size:8px;padding:5px 10px}

  .news{height:253px;text-align:center;padding-top:28px}
  .news .cards{display:flex;justify-content:space-between;width:542px;margin:24px auto 0}
  .card{width:259px;height:143px;border:1px solid #ddd;padding:3px;text-align:left;background:var(--white)}
  .card .photo{position:relative;height:100%;display:flex;flex-direction:column;justify-content:flex-end;padding:0 14px 11px;color:var(--white)}
  .card .photo.press{background:linear-gradient(160deg,#6c6f86 0%,#3b3d4e 45%,#24252f 100%)}
  .card .photo.gavel{background:linear-gradient(110deg,#1c1f2e 0%,#2a2e46 55%,#7a3b3a 78%,#b8b9c8 100%)}
  .card h3{font-family:"Cinzel",Georgia,serif;font-size:8px;line-height:12px;letter-spacing:.3px}
  .card time{font-size:5.5px;margin-top:7px}

  .site-footer{height:90px;background:var(--footer);color:var(--white);text-align:center;padding-top:24px}
  .footer-nav{font-family:"Cinzel",Georgia,serif;font-size:6.5px;letter-spacing:.3px;display:flex;justify-content:center;gap:5px}
  .footer-nav span.sep{color:#aaa}
  .social{display:flex;justify-content:center;gap:10px;margin-top:12px;font-size:6px}
  .social span{display:flex;align-items:center;gap:3px}
  .social span::before{content:"";width:5px;height:5px;border-radius:50%;background:var(--white)}
  .copyright{font-family:"Cinzel",Georgia,serif;font-size:5.5px;margin-top:10px}
</style>
</head>
<body>
  <div class="topbar">
    <div class="contact">
      <span><svg width="6" height="6" viewBox="0 0 10 10"><path d="M2 1l2 2-1 1.5c.8 1.4 1.6 2.2 3 3L7.5 6l2 2-1.5 1.5C4.5 9 1 5.5.5 2.5z" fill="#fff"/></svg>800 555 019</span>
      <span><svg width="6" height="7" viewBox="0 0 10 12"><path d="M5 0a4 4 0 0 1 4 4c0 3-4 8-4 8S1 7 1 4a4 4 0 0 1 4-4z" fill="none" stroke="#fff"/><circle cx="5" cy="4" r="1.4" fill="#fff"/></svg>hello@renatavote.org</span>
    </div>
    <div class="actions"><span>Donate</span><span>|</span><span>Join Volunteer</span></div>
  </div>

  <header class="site-header">
    <div class="brand"><span class="mark"></span><span class="name">RENATA</span></div>
    <nav class="main-nav">
      <a class="active" href="#">HOME</a><a href="#">ABOUT US</a><a href="#">NEWS</a><a href="#">EVENTS</a><a href="#">MEDIA</a><a href="#">CONTACT</a>
    </nav>
  </header>

  <section class="hero" role="img" aria-label="Smiling candidate portrait in front of a softly blurred flag">
    <div class="portrait"></div>
    <div class="copy">
      <div class="kicker">Remember to vote</div>
      <div class="date">August 30, 2016!</div>
      <div class="dots"><i class="on"></i><i></i><i></i></div>
    </div>
  </section>

  <section class="about">
    <h2 class="section-title">About <em>Renata</em></h2>
    <p>Renata grew up in the small river town of Millbrook, the daughter of a schoolteacher and a baker who later ran a busy family shop on Main Street. The first in her family to earn a degree, she studied history at Lakeview College and then went on to Harlow School of Law, where she graduated near the top of her class. Committed to fair and steady justice, she has spent many years in public service as a trial attorney and mediator, working to protect families and children across Pine and Cedar counties.</p>
    <a class="btn" href="#">Read More</a>
  </section>

  <section class="video-band" role="img" aria-label="Capitol building at dusk behind the campaign video">
    <h2 class="watch">WATCH VIDEO</h2>
    <div class="player">
      <div class="screen" role="img" aria-label="Video still of a capitol dome with flag stripes and stars"></div>
      <svg class="play" width="34" height="34" viewBox="0 0 34 34"><circle cx="17" cy="17" r="15" fill="rgba(0,0,0,.35)" stroke="#fff" stroke-width="2"/><path d="M13 10l11 7-11 7z" fill="#fff"/></svg>
      <div class="controls">
        <svg width="6" height="6" viewBox="0 0 10 10"><path d="M1 0l9 5-9 5z" fill="#fff"/></svg>
        <span>00:00 | 00:19</span>
        <div class="track"><b></b></div>
        <span>1×</span>
        <svg width="6" height="6" viewBox="0 0 10 10"><path d="M0 3h3l3-3v10L3 7H0z" fill="#fff"/></svg>
      </div>
    </div>
    <a class="btn" href="#">Donate Now</a>
  </section>

  <section class="news">
    <h2 class="section-title">Recent <em>News</em></h2>
    <div class="cards">
      <article class="card">
        <div class="photo press" role="img" aria-label="Press photographers at a campaign event before a flag">
          <h3>LOREM IPSUM DOLOR SIT AMET<br>CONSECTETUR</h3>
          <time>May 27,2016</time>
        </div>
      </article>
      <article class="card">
        <div class="photo gavel" role="img" aria-label="Wooden judge's gavel in front of a flag">
          <h3>LOREM IPSUM DOLOR SIT AMET<br>CONSECTETUR</h3>
          <time>May 27,2016</time>
        </div>
      </article>
    </div>
  </section>

  <footer class="site-footer">
    <nav class="footer-nav">
      <span>HOME</span><span class="sep">/</span><span>ABOUT US</span><span class="sep">/</span><span>NEWS</span><span class="sep">/</span><span>EVENTS</span><span class="sep">/</span><span>MEDIA</span><span class="sep">/</span><span>CONTACT</span>
    </nav>
    <div class="social"><span>Facely</span><span>Chirper</span><span>Workly</span><span>Circles</span></div>
    <div class="copyright">© 2016 Renata. All right Reserved.</div>
  </footer>
</body>
</html>
```